Business Card - high end, modern health care

Hey designers!

We need a double sided business card for the boutique, cutting edge physical therapy rehabilitation centre in Sydney's Northern Beaches.

With the most qualified physios in the area The Harbourview Motion Clinic does what other physiotherapy practices do not, we take our time with our patients giving them longer appointments, better physios and therefor faster results!

We guarantee that the service people receive at THMC will be unparalleled.

Hence we need a business card to reflect our modern, boutique, high end service. The final design needs to reflect that we are in a class of our own yet with the feel of beachside retreat.

Below I have attached our logo in both blue on white and white on blue. The exact colour is;
and the font that we have used in our logo is Tex Gyre Aventador.

I like the idea of the blue as the main colour as it is more eye catching and our signage onto the main road will be in this blue and in the interest of consistency across marketing the blue needs to be a part of the design. However I would appreciate a few designs onto a wooden background as this is a visual theme within the fitout of the practice.

The design needs to be of standard size (91x55mm).

Target Market(s)

We target people who have an end outcome in mind and those who have had poor experiences with other providers and ensure that everyone gets the care that they deserve with a premium service that is tailored to the individuals circumstances. As a premium service, the target market is highly educated, business and tech savvy with the additional target market of elderly people who have self funded their retirement and see value in paying for the best ongoing rehabilitation to maintain independence.

Industry/Entity Type

Physical Therapy

Contact Information for Business Card

Name, designation( Titled Musculoskeletal Physiotherapist... there will also be those in the company that have multiple designations ie 5 or 6 words long), phone number, email, facebook, instagram, address

Font styles to use
Sans Serif

Colors

Designer to choose colors to be used in the design.

Requirements
Must have
• Front - The logo as large as possible, blue or wooden theme, and all of the important details.
• Back - A blank space/lines on which to write appointment times (no "Appointment, date, time" etc.)
Nice to have
• facebook url
• logos for facebook and instagram
• Mini logos for the phone and email?

```html
<!DOCTYPE html>
<html lang="en">
<head>
<meta charset="utf-8">
<title>The Harbourview Motion Clinic – Business Card</title>
<link rel="stylesheet" href="https://fonts.googleapis.com/css2?family=Raleway:wght@400;500;600;800&display=swap">
<style>
  :root {
    --brand-blue: #0f4fa8;
    --accent-blue: #1c5fc4;
    --faint-blue: #dfe2f1;
    --ink: #1b1b1b;
    --rule: #2a2a2a;
    --card: #fbfbfb;
    --backdrop: #e9e8e6;
    --facebook-dot: #1e8fd6;
    --instagram-dot: #ec5e9c;
  }
  * { box-sizing: border-box; margin: 0; padding: 0; }
  html, body { width: 1200px; height: 1200px; overflow: hidden; }
  body {
    background: var(--backdrop);
    font-family: "Raleway", sans-serif;
    color: var(--ink);
    display: flex;
    flex-direction: column;
    align-items: center;
    justify-content: center;
    gap: 44px;
  }
  .card {
    position: relative;
    width: 900px;
    height: 544px;
    background: var(--card);
    border-radius: 4px;
    box-shadow: 0 10px 28px rgba(0,0,0,.12);
    overflow: hidden;
  }

  /* Logo side */
  .brand-lockup {
    position: absolute;
    left: 70px;
    top: 110px;
    display: flex;
    align-items: center;
    gap: 18px;
    z-index: 2;
  }
  .brand-mark {
    width: 62px; height: 62px;
    border-radius: 50%;
    background: var(--brand-blue);
    flex: none;
  }
  .brand-name {
    font-weight: 800;
    font-size: 34px;
    line-height: 1.05;
    letter-spacing: 1px;
    text-transform: uppercase;
    color: var(--brand-blue);
  }
  .faint-circle {
    position: absolute;
    right: 30px;
    top: 130px;
    width: 500px;
    height: 500px;
    border-radius: 50%;
    background: var(--faint-blue);
    z-index: 1;
  }

  /* Details side */
  .person-name {
    position: absolute;
    left: 90px; top: 62px;
    font-size: 40px;
    font-weight: 400;
  }
  .person-name .highlight { color: var(--accent-blue); }
  .designation {
    position: absolute;
    left: 92px; top: 116px;
    font-size: 18px;
  }
  .divider {
    position: absolute;
    left: 80px;
    width: 500px;
    height: 1.5px;
    background: var(--rule);
  }
  .divider.upper { top: 160px; }
  .divider.lower { top: 290px; }
  .contact-list {
    position: absolute;
    left: 84px; top: 184px;
    list-style: none;
    display: flex;
    flex-direction: column;
    gap: 18px;
    font-size: 24px;
  }
  .contact-list li { display: flex; align-items: center; gap: 18px; }
  .contact-list svg { width: 28px; height: 28px; flex: none; }
  .social-row {
    position: absolute;
    left: 84px; top: 318px;
    display: flex;
    gap: 150px;
    font-size: 21px;
  }
  .social { display: flex; align-items: center; gap: 14px; }
  .social-dot { width: 26px; height: 26px; border-radius: 50%; flex: none; }
  .social-dot.facebook { background: var(--facebook-dot); }
  .social-dot.instagram { background: var(--instagram-dot); }
  .appointment-line {
    position: absolute;
    left: 80px; right: 60px; bottom: 80px;
    border-top: 1.5px dashed #9a9a9a;
  }
  .corner-logo {
    position: absolute;
    right: 70px; top: 250px;
    display: flex;
    flex-direction: column;
    align-items: center;
    gap: 14px;
  }
  .corner-logo .brand-mark { width: 160px; height: 160px; }
  .corner-logo .brand-name {
    font-size: 15px;
    text-align: center;
    letter-spacing: .5px;
  }
</style>
</head>
<body>

  <section class="card card-front" aria-label="Logo side">
    <div class="brand-lockup">
      <div class="brand-mark" aria-hidden="true"></div>
      <div class="brand-name">The Harbourview<br>Motion Clinic</div>
    </div>
    <div class="faint-circle" aria-hidden="true"></div>
  </section>

  <section class="card card-details" aria-label="Contact side">
    <h1 class="person-name">Name of <span class="highlight">Person</span></h1>
    <p class="designation">Designation</p>
    <div class="divider upper"></div>

    <ul class="contact-list">
      <li>
        <svg viewBox="0 0 24 24" aria-hidden="true">
          <circle cx="12" cy="12" r="10" fill="none" stroke="#1b1b1b" stroke-width="2"/>
          <path d="M9 7.5c-1 .5-1.5 1.5-1.2 3 .5 2.5 2.3 4.6 4.5 5.7 1.3.6 2.5.4 3.2-.5l-1.6-1.6-1.3.6c-1.2-.6-2.1-1.6-2.6-2.8l.7-1.2z" fill="#1b1b1b"/>
        </svg>
        <span>555.018.4127</span>
      </li>
      <li>
        <svg viewBox="0 0 24 24" aria-hidden="true">
          <rect x="2" y="5" width="20" height="14" fill="#1b1b1b"/>
          <path d="M2 5l10 8 10-8M2 19l7-7M22 19l-7-7" fill="none" stroke="#fbfbfb" stroke-width="1.4"/>
        </svg>
        <span>hello@harbourviewmotion.com</span>
      </li>
    </ul>
    <div class="divider lower"></div>

    <div class="social-row">
      <div class="social"><span class="social-dot facebook" aria-hidden="true"></span><span>facebook/name</span></div>
      <div class="social"><span class="social-dot instagram" aria-hidden="true"></span><span>instagram_name</span></div>
    </div>

    <div class="appointment-line" aria-hidden="true"></div>

    <div class="corner-logo">
      <div class="brand-mark" aria-hidden="true"></div>
      <div class="brand-name">The Harbourview<br>Motion Clinic</div>
    </div>
  </section>

</body>
</html>
```